Executive Business Card for Healthcare Company [Need Today]

I need a business card design for a healthcare company. The only branding the company has thus far is a logo. The cards will be utilized by company executives. The design I envision will be vibrant and appealing but with a corporate feel. They shouldn't be too casual or playful. I would like to complete this project TODAY if possible.

Target Market(s)

Healthcare vendors, other executives in healthcare and pharmaceuticals

Industry/Entity Type

Pharmaceutical

Contact Information for Business Card

See attachment

Font styles to use
Serif
Sans Serif

Colors

Designer to choose colors to be used in the design.

```html
<!DOCTYPE html>
<html lang="en">
<head>
<meta charset="utf-8">
<title>Corvane Therapeutics – Business Card</title>
<link rel="stylesheet" href="https://fonts.googleapis.com/css2?family=Crimson+Text:wght@400;600&family=Open+Sans:wght@300;400&display=swap">
<style>
  :root {
    --backdrop: #8fa8ad;
    --paper: #ffffff;
    --green: #6cc59a;
    --teal: #3bbfcb;
    --ink: #1d1d1d;
    --grey: #6b6b6b;
    --icon: #222a2c;
  }
  * { margin: 0; padding: 0; box-sizing: border-box; }
  html, body { width: 1200px; height: 800px; overflow: hidden; }
  body { background: var(--backdrop); position: relative; font-family: "Crimson Text", serif; }

  .card { position: absolute; left: 326px; width: 538px; height: 307px; background: var(--paper); overflow: hidden; }
  .card--front { top: 24px; }
  .card--back { top: 426px; }

  /* Front */
  .front-frame { position: absolute; inset: 0; border: 9px solid transparent;
    border-image: linear-gradient(180deg, var(--green), var(--teal)) 1; }
  .brand-ring { position: absolute; left: 70px; top: 50px; width: 128px; height: 128px;
    border: 5px solid var(--green); border-radius: 50%; }
  .brand-divider { position: absolute; left: 213px; top: 90px; width: 1px; height: 66px; background: var(--grey); }
  .brand-name { position: absolute; left: 228px; top: 62px; font-family: "Crimson Text", serif;
    font-weight: 400; font-size: 62px; line-height: 1; color: var(--teal); letter-spacing: 1px; }
  .brand-tagline { position: absolute; right: 58px; top: 134px; font-family: "Open Sans", sans-serif;
    font-weight: 300; font-size: 26px; color: var(--grey); }
  .find-us { position: absolute; left: 0; right: 0; top: 202px; text-align: center; font-size: 17px; color: var(--ink); }
  .social-row { position: absolute; left: 0; right: 0; top: 230px; display: flex; justify-content: center; gap: 8px; }
  .social-row span { width: 18px; height: 18px; background: var(--teal); border-radius: 3px; }
  .front-web { position: absolute; left: 0; right: 0; top: 282px; text-align: center; font-size: 14px; color: var(--teal); }

  /* Back */
  .feature-ring { position: absolute; left: -38px; top: 0; width: 272px; height: 272px;
    border: 8px solid var(--green); border-radius: 50%; }
  .feature-name { position: absolute; left: 8px; top: 112px; font-size: 46px; color: var(--teal); }
  .person-name { position: absolute; left: 266px; top: 26px; font-size: 38px; font-weight: 400; color: var(--ink); line-height: 1; }
  .person-title { position: absolute; left: 267px; top: 71px; font-size: 19px; color: var(--ink); }
  .contact-row { position: absolute; left: 266px; display: flex; align-items: center; gap: 12px;
    font-family: "Open Sans", sans-serif; font-size: 18px; color: var(--ink); }
  .contact-row svg { width: 27px; height: 27px; flex: none; }
  .contact-row--mobile { top: 118px; }
  .contact-row--office { top: 158px; }
  .contact-row--email { top: 196px; font-size: 16px; }
  .contact-row--address { top: 240px; align-items: flex-start; gap: 6px;
    font-family: "Crimson Text", serif; font-size: 16px; line-height: 1.2; }
  .contact-row--address svg { width: 25px; height: 25px; margin-top: -2px; }
  .back-rule { position: absolute; top: 294px; height: 5px;
    background: linear-gradient(90deg, var(--teal), var(--green)); }
  .back-rule--left { left: 0; width: 192px; }
  .back-rule--right { left: 347px; width: 191px; }
  .back-web { position: absolute; left: 192px; width: 155px; top: 285px; text-align: center; font-size: 15px; color: var(--ink); }
</style>
</head>
<body>
  <section class="card card--front">
    <div class="front-frame"></div>
    <div class="brand-ring"></div>
    <div class="brand-divider"></div>
    <div class="brand-name">corvane</div>
    <div class="brand-tagline">therapeutics</div>
    <p class="find-us">Find Us on:</p>
    <div class="social-row"><span></span><span></span><span></span><span></span></div>
    <p class="front-web">www.website.com</p>
  </section>

  <section class="card card--back">
    <div class="feature-ring"></div>
    <div class="feature-name">corvane</div>
    <h1 class="person-name">Daniel Hurst</h1>
    <p class="person-title">Senior Director of Marketing</p>

    <div class="contact-row contact-row--mobile">
      <svg viewBox="0 0 28 28"><circle cx="14" cy="14" r="14" fill="var(--icon)"/>
        <path d="M9 7.5c.8-.6 1.7-.4 2.1.4l1.1 2.3c.3.6.1 1.2-.4 1.6l-.9.7c.7 1.7 2 3 3.7 3.8l.7-.9c.4-.5 1-.7 1.6-.4l2.3 1.1c.8.4 1 1.3.4 2.1l-.9 1.1c-.6.7-1.6 1-2.5.6-3.8-1.5-6.8-4.5-8.3-8.3-.3-.9-.1-1.9.6-2.5z" fill="#fff"/></svg>
      <span>555-201-4482</span>
    </div>
    <div class="contact-row contact-row--office">
      <svg viewBox="0 0 28 28"><circle cx="14" cy="14" r="14" fill="var(--icon)"/>
        <path d="M6.5 11c0-2 3.4-3 7.5-3s7.5 1 7.5 3v1.2h-3.2V10.8h-8.6v1.4H6.5z" fill="#fff"/>
        <path d="M9 13h10l2 6H7z" fill="#fff"/><circle cx="14" cy="16" r="1.6" fill="var(--icon)"/></svg>
      <span>555-201-7730</span>
    </div>
    <div class="contact-row contact-row--email">
      <svg viewBox="0 0 28 28"><circle cx="14" cy="14" r="14" fill="var(--icon)"/>
        <rect x="7" y="9.5" width="14" height="9" fill="#fff"/>
        <path d="M7 9.5l7 5.2 7-5.2" fill="none" stroke="var(--icon)" stroke-width="1"/></svg>
      <span>dhurst@corvanerx.com</span>
    </div>
    <div class="contact-row contact-row--address">
      <svg viewBox="0 0 28 28"><circle cx="14" cy="14" r="14" fill="var(--icon)"/>
        <path d="M14 6a5 5 0 0 1 5 5c0 3.6-5 10-5 10s-5-6.4-5-10a5 5 0 0 1 5-5z" fill="#fff"/>
        <circle cx="14" cy="11" r="1.8" fill="var(--icon)"/></svg>
      <span>118 Linden Avenue Marlow<br>GA 30690</span>
    </div>

    <div class="back-rule back-rule--left"></div>
    <p class="back-web">www.website.com</p>
    <div class="back-rule back-rule--right"></div>
  </section>
</body>
</html>
```